I have a business that exists already (Linden Conservatory of Music) that we offer music lessons to all instruments. I recently opened a smaller version called CHORDS by Linden that will only teach piano lessons. What I'm looking for now is a 3 page Website on word press. After I choose the design I like I want to be able to take over the website and bring it to our hosting company. We want full control of it and our team will take over. The reason I'm doing this is to have other visions and ideas from others. The first page will be about the company and our message/vision. Second page about the piano lessons. The third will be about franchising this concept "Chords by Linden" Attached are 3 Logos . Please refer to our existing website www.lindenmusicconservatory.example to look at our piano page and franchising page. Please feel free to message me if you need more info. Thanks
Please note I do not want the new website (Chords by Linden) To look like the other Website (Linden Conservatory of Music) Fresh new look. I do not want the colours red or using the Red logo. I only provided it so that you have an Idea of What the other business looks like and that you can take the piano content and franchise content off of it. Chords by Linden is smaller concept and only piano lessons.
Thanks
Only Piano lessons for all students
3 page

```html
<!DOCTYPE html>
<html lang="en">
<head>
<meta charset="utf-8">
<title>Chords by Linden</title>
<link href="https://fonts.googleapis.com/css2?family=Cinzel:wght@400;500&family=Great+Vibes&family=Montserrat:wght@400;500&display=swap" rel="stylesheet">
<style>
:root{
  --gold:#e5c464;
  --gold-deep:#d6b04a;
  --ink:#111111;
  --black:#000000;
  --white:#ffffff;
  --mist:#ececec;
  --mist-2:#f4f4f4;
  --slate:#4b4b4b;
  --text:#2a2a2a;
}
*{margin:0;padding:0;box-sizing:border-box}
html,body{width:1200px;height:2893px;overflow:hidden}
body{position:relative;background:var(--white);font-family:"Montserrat",sans-serif;color:var(--text)}
.abs{position:absolute}
.serif{font-family:"Cinzel",serif}
.btn{position:absolute;display:flex;align-items:center;justify-content:center;font-family:"Cinzel",serif;font-size:13.5px;font-weight:500;border-radius:2px;letter-spacing:.2px}
.btn-gold{background:var(--gold);color:var(--ink)}
.btn-dark{background:var(--black);color:var(--white)}
.rule{position:absolute;height:2px;width:36px}

/* header */
.site-header{left:0;top:0;width:1200px;height:78px;background:var(--black);z-index:3}
.brand{left:147px;top:22px;display:flex;align-items:center;gap:8px;color:var(--white);font-family:"Cinzel",serif;font-size:24px}
.brand-mark{width:12px;height:12px;background:var(--gold);border-radius:50%}
.nav{top:32px;display:flex;font-family:"Cinzel",serif;font-size:12.5px;color:var(--white)}
.nav a{position:absolute;white-space:nowrap;color:inherit;text-decoration:none}
.nav a.active{color:var(--gold)}
.nav-divider{left:922px;top:23px;width:1px;height:30px;background:#555}
.social-dot{top:34px;width:11px;height:11px;border-radius:50%;background:var(--gold)}

/* hero */
.hero{left:0;top:0;width:1200px;height:600px;background:radial-gradient(ellipse at 78% 40%,#7a5a3a 0%,#3a2618 25%,#15100c 55%,#050505 100%)}
.hero-welcome{left:141px;top:215px;font-family:"Great Vibes",cursive;font-size:72px;color:var(--gold);line-height:1}
.hero-title{left:141px;top:302px;font-family:"Cinzel",serif;font-size:52px;color:var(--white);letter-spacing:.5px;line-height:1}

/* about */
.about{left:0;top:600px;width:1200px;height:439px}
.about-photo{left:141px;top:69px;width:415px;height:300px;border-radius:10px;background:linear-gradient(135deg,#d8d2c8,#8d8476 55%,#3e3a34)}
.about-copy{left:601px;top:66px;width:456px}
.about-copy h2{font-family:"Cinzel",serif;font-weight:400;font-size:25px;color:var(--ink)}
.about-copy h3{font-weight:500;font-size:15.5px;color:var(--ink);margin-top:24px}
.about-copy p{font-size:12.6px;line-height:19px;text-align:justify;color:var(--ink);margin-top:5px}

/* vision */
.vision{left:0;top:1039px;width:1200px;height:376px;background:linear-gradient(180deg,var(--mist-2),var(--mist));text-align:center}
.vision h2{position:absolute;left:0;width:1200px;top:62px;font-family:"Cinzel",serif;font-weight:400;font-size:24px;color:var(--ink)}
.vision p{position:absolute;left:144px;width:912px;font-size:13.4px;line-height:21.7px;color:var(--ink)}

/* programs */
.programs{left:0;top:1415px;width:1200px;height:469px}
.programs h2{position:absolute;left:141px;top:65px;font-family:"Cinzel",serif;font-weight:400;font-size:24px;line-height:34px;color:var(--ink)}
.program-list{position:absolute;left:141px;top:162px;width:450px;list-style:none;font-size:12.6px;line-height:19px;color:#333}
.program-list li{position:relative;padding-left:26px;margin-bottom:9px}
.program-list svg{position:absolute;left:0;top:3px}
.programs-photo{left:644px;top:67px;width:414px;height:327px;border-radius:10px;background:linear-gradient(90deg,#141210 0%,#3b322a 35%,#d9cfc2 70%,#efe9e1)}

/* franchise */
.franchise{left:0;top:1884px;width:1200px;height:269px;background:linear-gradient(180deg,#e6e6e6,var(--mist-2));text-align:center}
.franchise h2{position:absolute;left:0;width:1200px;top:64px;font-family:"Cinzel",serif;font-weight:400;font-size:34px;color:var(--ink)}
.franchise p{position:absolute;left:0;width:1200px;top:125px;font-size:15.5px;color:#444;letter-spacing:.2px}

/* booking */
.booking{left:0;top:2153px;width:1200px;height:476px;background:linear-gradient(180deg,#0c0c0c 0%,#2a2a2a 35%,var(--slate) 42%,var(--slate) 100%)}
.booking h2{position:absolute;left:0;width:1200px;top:64px;text-align:center;font-family:"Cinzel",serif;font-weight:400;font-size:24px;color:var(--white)}
.booking-card{left:141px;top:137px;width:917px;height:272px;background:var(--white)}
.field{position:absolute;background:var(--white);box-shadow:0 2px 8px rgba(0,0,0,.12);font-size:11.5px;color:#777;padding:12px 14px;border-radius:2px}

/* contact */
.contact{left:0;top:2629px;width:1200px;height:264px;background:var(--gold)}
.contact-item{position:absolute;width:340px;text-align:center;color:var(--ink)}
.contact-item svg{display:block;margin:0 auto}
.contact-item h4{font-family:"Cinzel",serif;font-weight:400;font-size:15px;margin-top:10px}
.contact-item p{font-size:12.6px;line-height:20px;margin-top:2px}
.contact-rule{left:141px;top:214px;width:917px;height:1px;background:rgba(0,0,0,.35)}
.copyright{left:141px;top:231px;font-size:12.6px;color:var(--ink)}
.footer-social{top:223px;width:31px;height:31px;border-radius:50%;background:var(--black)}
</style>
</head>
<body>

<section class="abs hero" role="img" aria-label="Photo of a young woman playing a grand piano on a dimly lit stage"></section>
<div class="abs hero-welcome">Welcome to</div>
<h1 class="abs hero-title">CHORDS BY LINDEN</h1>
<div class="btn btn-gold" style="left:141px;top:390px;width:115px;height:35px">READ MORE</div>

<header class="abs site-header">
  <div class="abs brand"><span class="brand-mark"></span>Chords by Linden</div>
  <nav class="abs nav" style="left:0;width:1200px">
    <a class="active" style="left:460px">HOME</a>
    <a style="left:544px">PIANO LESSONS</a>
    <a style="left:683px">FRANCHISING</a>
    <a style="left:811px">CONTACT US</a>
  </nav>
  <div class="abs nav-divider"></div>
  <span class="abs social-dot" style="left:951px"></span>
  <span class="abs social-dot" style="left:983px"></span>
  <span class="abs social-dot" style="left:1016px"></span>
  <span class="abs social-dot" style="left:1048px"></span>
</header>

<section class="abs about">
  <svg class="abs" style="left:0;top:0" width="1200" height="439"><polygon points="562,0 1200,0 1200,439 450,439" fill="var(--gold)"/></svg>
  <div class="abs about-photo" role="img" aria-label="Photo of a young man with headphones playing a keyboard in a home studio"></div>
  <div class="abs about-copy">
    <h2>ABOUT US</h2>
    <div class="rule" style="background:var(--ink);position:relative;margin-top:7px"></div>
    <h3>Playing The Piano</h3>
    <p>When you think of a piano, you probably envision black and white keys but the piano is more than those harmonious sounds created by the player. The versatility and the musicianship instilled into the player from those keys is the true magic that comes from playing piano! Starting from the grassroots, experience different methods and styles of playing piano. To mark the milestones of progression, engage in one of Linden's many unique performance opportunities like annual festival competitions, recitals or our examinations (Linden &amp; LCE). Penultimately,</p>
  </div>
  <div class="btn btn-dark" style="left:600px;top:333px;width:115px;height:34px">READ MORE</div>
</section>

<section class="abs vision">
  <h2>OUR VISION</h2>
  <div class="rule" style="left:582px;top:104px;background:var(--gold)"></div>
  <p style="top:120px">Our Mission Lorem ipsum dolor sit amet, consectetur adipiscing elit, sed do eiusmod tempor incididunt ut labore et dolore magna aliqua. Ut enim ad minim veniam, quis nostrud exercitation ullamco laboris nisi ut aliquip ex ea commodo consequat. Duis aute irure dolor in reprehenderit in voluptate velit esse cillum dolore eu fugiat nulla pariatur. Excepteur sint occaecat cupidatat non proident, sunt in culpa qui officia deserunt mollit anim id est laborum.</p>
  <p style="top:207px">Ut enim ad minim veniam, quis nostrud exercitation ullamco laboris nisi ut aliquip ex ea commodo consequat. Duis aute irure dolor in reprehenderit in voluptate velit esse cillum dolore eu fugiat nulla pariatur.</p>
  <div class="btn btn-gold" style="left:543px;top:269px;width:114px;height:35px">READ MORE</div>
</section>

<section class="abs programs">
  <svg class="abs" style="left:0;top:0" width="1200" height="469"><polygon points="0,0 721,0 827,469 0,469" fill="var(--gold)"/></svg>
  <h2>OUR PROGRAMS ALSO PROVIDE<br>STUDENTS THE OPPORTUNITY TO:</h2>
  <div class="rule" style="left:141px;top:142px;background:var(--ink)"></div>
  <ul class="program-list">
    <li><svg width="15" height="12" viewBox="0 0 15 12"><path d="M1 6h9M7 2l4 4-4 4" stroke="#222" stroke-width="1.5" fill="none"/></svg>Participate in large-scale performances.</li>
    <li><svg width="15" height="12" viewBox="0 0 15 12"><path d="M1 6h9M7 2l4 4-4 4" stroke="#222" stroke-width="1.5" fill="none"/></svg>Perform at Linden's many community events on a regular basis.</li>
    <li><svg width="15" height="12" viewBox="0 0 15 12"><path d="M1 6h9M7 2l4 4-4 4" stroke="#222" stroke-width="1.5" fill="none"/></svg>Access the GTA's coolest Broadcast stage</li>
    <li><svg width="15" height="12" viewBox="0 0 15 12"><path d="M1 6h9M7 2l4 4-4 4" stroke="#222" stroke-width="1.5" fill="none"/></svg>Attend Clinics, Masterclasses, and Jam Nights</li>
    <li><svg width="15" height="12" viewBox="0 0 15 12"><path d="M1 6h9M7 2l4 4-4 4" stroke="#222" stroke-width="1.5" fill="none"/></svg>Access the Linden Rocks band program. Linden's Band Program empowers and electrifies students to come together, create music and confidently hit the stage with their own band identity while having fun and honing their instrument.</li>
  </ul>
  <div class="btn btn-dark" style="left:141px;top:1775px;margin-top:-1415px;width:115px;height:34px">READ MORE</div>
  <div class="abs programs-photo" role="img" aria-label="Close-up photo of hands playing piano keys"></div>
</section>

<section class="abs franchise">
  <h2>FRANCHISE OPPORTUNITIES</h2>
  <p>Be Part Of The Linden Conservatory Family</p>
  <div class="btn btn-gold" style="left:543px;top:163px;width:114px;height:35px">READ MORE</div>
</section>

<section class="abs booking">
  <h2>BOOK A MEETING WITH US</h2>
  <div class="rule" style="left:582px;top:100px;background:var(--gold)"></div>
  <div class="abs booking-card">
    <div class="field" style="left:48px;top:32px;width:267px;height:38px">Your Name*</div>
    <div class="field" style="left:324px;top:32px;width:269px;height:38px">Your Phone*</div>
    <div class="field" style="left:605px;top:32px;width:267px;height:38px">Your Email*</div>
    <div class="field" style="left:48px;top:85px;width:824px;height:88px">Your Message*</div>
    <div class="btn btn-gold" style="left:402px;top:200px;width:114px;height:35px">SUBMIT</div>
  </div>
</section>

<footer class="abs contact">
  <div class="contact-item" style="left:86px;top:52px">
    <svg width="44" height="44" viewBox="0 0 24 24"><path d="M6.6 10.8a15 15 0 0 0 6.6 6.6l2.2-2.2a1 1 0 0 1 1-.25 11.4 11.4 0 0 0 3.6.57 1 1 0 0 1 1 1V20a1 1 0 0 1-1 1A17 17 0 0 1 3 4a1 1 0 0 1 1-1h3.5a1 1 0 0 1 1 1c0 1.25.2 2.45.57 3.57a1 1 0 0 1-.25 1z" fill="var(--ink)"/><path d="M14 3a7 7 0 0 1 7 7M14 6.5a3.5 3.5 0 0 1 3.5 3.5" stroke="var(--ink)" stroke-width="1.6" fill="none"/></svg>
    <h4>CALL US</h4>
    <p>1-555-014-2290</p>
  </div>
  <div class="contact-item" style="left:430px;top:46px">
    <svg width="40" height="52" viewBox="0 0 24 32"><path d="M12 0C5.4 0 0 5.2 0 11.8 0 20 12 32 12 32s12-12 12-20.2C24 5.2 18.6 0 12 0zm0 17a5.5 5.5 0 1 1 0-11 5.5 5.5 0 0 1 0 11z" fill="var(--ink)"/></svg>
    <h4>POSTAL ADDRESS</h4>
    <p>123, Lorem ipsum dolor sit 123456<br>#123456 Lorem ipsum</p>
  </div>
  <div class="contact-item" style="left:740px;top:60px">
    <svg width="46" height="36" viewBox="0 0 46 36"><rect x="1" y="1" width="44" height="34" rx="3" fill="var(--ink)"/><path d="M3 4l20 16L43 4" stroke="var(--gold)" stroke-width="2.5" fill="none"/></svg>
    <h4>E-MAIL</h4>
    <p>info@chordslindenmusic.example</p>
  </div>
  <div class="abs contact-rule"></div>
  <div class="abs copyright">Copyright 2019. Chordslinden Music Training. All rights reserved.</div>
  <span class="abs footer-social" style="left:949px"></span>
  <span class="abs footer-social" style="left:988px"></span>
  <span class="abs footer-social" style="left:1027px"></span>
</footer>

</body>
</html>
```